Need Business Card for our Real Estate Business with Sales Executive's Picture

PANTONE 484 C ( RED)

PANTONE 2766 C ( BLUE

Industry/Entity Type

Real Estate

Contact Information for Business Card

Name, Mobile, email, & picture of Person
Agency Phone, address, Web address

Requirements
Must have
• Our Logo Colours, Agent Picture,

```html
<!DOCTYPE html>
<html lang="en">
<head>
<meta charset="utf-8">
<title>Northgate Real Estate – Business Card</title>
<link href="https://fonts.googleapis.com/css2?family=Cinzel:wght@500;600&family=Crimson+Text:wght@400;600&display=swap" rel="stylesheet">
<style>
  :root{
    --navy:#101c4c;
    --maroon:#7a1622;
    --white:#ffffff;
    --stage:#e6e7ea;
    --ink:#1c2350;
  }
  *{margin:0;padding:0;box-sizing:border-box}
  html,body{width:1200px;height:800px;overflow:hidden;background:var(--stage)}
  .stage{position:relative;width:1200px;height:800px}
  .card{position:absolute;top:245px;width:540px;height:310px;background:var(--white);overflow:hidden;box-shadow:0 10px 30px rgba(0,0,0,.18)}
  .card--front{left:40px}
  .card--back{left:620px}
  .card svg.shapes{position:absolute;inset:0}
  .house-photo{position:absolute;inset:0;background:linear-gradient(160deg,#f4f4f5 0%,#e3e4e6 45%,#eeeeef 100%)}
  .agent-photo{position:absolute;left:95px;top:95px;width:185px;height:215px;background:linear-gradient(180deg,#d9c6b8 0%,#c7ad9b 28%,#2c3f86 45%,#1f2f6e 100%);border-radius:90px 90px 0 0}
  .brand{position:absolute;text-align:center;color:var(--navy);font-family:"Cinzel",serif;font-weight:600;line-height:1}
  .brand__name{font-size:30px;letter-spacing:2px}
  .brand__sub{font-size:10px;letter-spacing:4px;margin-top:6px}
  .card--front .brand{left:290px;top:36px;width:230px}
  .card--back .brand{left:295px;top:92px;width:230px}
  .person{position:absolute;font-family:"Cinzel",serif;color:var(--navy)}
  .person__name{font-size:15px;font-weight:600;letter-spacing:.5px;white-space:nowrap}
  .person__role{font-family:"Crimson Text",serif;color:var(--maroon);font-size:12px;line-height:1}
  .card--front .person{left:300px;top:92px;text-align:center;width:160px}
  .social{position:absolute;left:330px;top:232px;display:flex;gap:8px}
  .social span{width:18px;height:18px;background:var(--white);border-radius:2px}
  .card--back .person{left:140px;top:218px}
  .rule{position:absolute;height:1px;background:var(--maroon)}
  .contact{position:absolute;top:258px;font-family:"Crimson Text",serif;font-size:11px;color:var(--ink);line-height:17px}
  .contact__item{display:flex;align-items:center;gap:6px;white-space:nowrap}
  .contact__item svg{width:12px;height:12px;flex:none}
  .divider{position:absolute;top:260px;width:1px;height:32px;background:var(--maroon)}
</style>
</head>
<body>
<main class="stage">

  <section class="card card--front">
    <div class="house-photo" role="img" aria-label="Faded photo of a large white house"></div>
    <svg class="shapes" viewBox="0 0 540 310" aria-hidden="true">
      <polygon points="150,310 540,92 540,112 180,310" fill="var(--maroon)"/>
      <polygon points="180,310 540,112 540,310" fill="var(--navy)"/>
      <polygon points="0,282 0,310 48,310" fill="var(--maroon)"/>
    </svg>
    <div class="agent-photo" role="img" aria-label="Photo of the sales agent in a blue suit"></div>
    <div class="brand">
      <div class="brand__name">NORTHGATE</div>
      <div class="brand__sub">REAL ESTATE</div>
    </div>
    <div class="person">
      <div class="person__name">DANIEL BROOKS</div>
      <div class="person__role">Owner</div>
    </div>
    <div class="social"><span></span><span></span></div>
  </section>

  <section class="card card--back">
    <svg class="shapes" viewBox="0 0 540 310" aria-hidden="true">
      <rect width="540" height="310" fill="var(--navy)"/>
      <polygon points="48,310 244,44 540,44 540,62 254,62 72,310" fill="var(--maroon)"/>
      <polygon points="72,310 254,62 540,62 540,310" fill="var(--white)"/>
    </svg>
    <div class="brand">
      <div class="brand__name">NORTHGATE</div>
      <div class="brand__sub">REAL ESTATE</div>
    </div>
    <div class="rule" style="left:300px;top:160px;width:220px"></div>
    <div class="person">
      <div class="person__name">DANIEL BROOKS</div>
      <div class="person__role">Owner</div>
    </div>
    <div class="rule" style="left:135px;top:252px;width:390px"></div>

    <div class="contact" style="left:140px">
      <div class="contact__item">
        <svg viewBox="0 0 12 12"><circle cx="6" cy="6" r="5.4" fill="none" stroke="var(--maroon)"/><rect x="4" y="3" width="4" height="6" rx="1" fill="none" stroke="var(--maroon)" stroke-width=".9"/></svg>
        (555) 014-2286</div>
      <div class="contact__item">
        <svg viewBox="0 0 12 12"><circle cx="6" cy="6" r="5.4" fill="none" stroke="var(--maroon)"/><rect x="4" y="3" width="4" height="6" rx="1" fill="none" stroke="var(--maroon)" stroke-width=".9"/></svg>
        (555) 014-2287</div>
    </div>
    <div class="divider" style="left:240px"></div>
    <div class="contact" style="left:252px">
      <div class="contact__item">
        <svg viewBox="0 0 12 12"><circle cx="6" cy="6" r="5.4" fill="var(--maroon)"/><rect x="3.2" y="4" width="5.6" height="4" fill="none" stroke="#fff" stroke-width=".8"/><polyline points="3.2,4 6,6.2 8.8,4" fill="none" stroke="#fff" stroke-width=".8"/></svg>
        info@northgatehomes.com</div>
      <div class="contact__item">
        <svg viewBox="0 0 12 12"><circle cx="6" cy="6" r="5.4" fill="var(--maroon)"/><circle cx="6" cy="6" r="3" fill="none" stroke="#fff" stroke-width=".8"/><line x1="3" y1="6" x2="9" y2="6" stroke="#fff" stroke-width=".8"/><line x1="6" y1="3" x2="6" y2="9" stroke="#fff" stroke-width=".8"/></svg>
        www.northgatehomes.com</div>
    </div>
    <div class="divider" style="left:395px"></div>
    <div class="contact" style="left:407px">
      <div>PO BOX 48 Harbour Lane</div>
      <div>5th Street Ashford</div>
    </div>
  </section>

</main>
</body>
</html>
```